Private Dining Restaurant Menu Design

Looking for help in designing a private dining room menu brochure - probably would need 4 panel layout to make all of the content fit, or a 5.5x8" booklet. Open to your ideas on layout/vessel - would want to post on website and be able to print to hand out to guests interested in booking our private dining room.

All content is in the attached "Private Dining Menu".

Would like to match existing dinner menu design - also attached.

Website is www.copperkettlebistro.com

Requirements
Must have
• Easy to read format of a brochure of the private dining menu content - want to be able to hand out to interested guests and have it simple and easy to read/flip through.

```html
<!DOCTYPE html>
<html lang="en">
<head>
<meta charset="utf-8">
<title>Copper Kettle – Private Dining Room</title>
<link href="https://fonts.googleapis.com/css2?family=Merriweather:wght@400;700&family=Open+Sans:wght@400&family=Russo+One&display=swap" rel="stylesheet">
<style>
  :root {
    --night: #25232a;
    --paper: #ffffff;
    --gold: #e9c96f;
    --gold-deep: #b98a2c;
    --gold-light: #f6e3a4;
    --ink-light: #f4f2ee;
    --brand-red: #7b2b22;
  }
  * { margin: 0; padding: 0; box-sizing: border-box; }
  html, body { width: 849px; height: 1200px; overflow: hidden; background: var(--night); }
  .sheet {
    position: relative; width: 849px; height: 1200px; overflow: hidden;
    background: var(--night); color: var(--ink-light);
    font-family: "Merriweather", Georgia, serif;
  }
  .backdrop { position: absolute; inset: 0; }
  .brand {
    position: absolute; left: 505px; top: 128px; width: 295px;
    text-align: center; color: var(--brand-red);
    font-family: "Merriweather", Georgia, serif; font-weight: 700;
    font-size: 33px; letter-spacing: 1px; line-height: 1.2;
  }
  .page-title {
    position: absolute; left: 56px; top: 266px;
    font-family: "Russo One", sans-serif; font-size: 39px; line-height: 44px;
    letter-spacing: 3.6px; white-space: nowrap;
    background: linear-gradient(180deg, var(--gold-light) 0%, var(--gold) 45%, var(--gold-deep) 100%);
    -webkit-background-clip: text; background-clip: text; color: transparent;
  }
  .block {
    position: absolute; left: 56px; width: 730px;
    font-size: 15px; line-height: 21.5px;
  }
  .intro { top: 329px; width: 690px; line-height: 22px; }
  .section-head { font-weight: 700; font-size: 20.5px; line-height: 26px; white-space: nowrap; }
  .minimum-head { top: 444px; }
  .meals { top: 471px; line-height: 22px; }
  .meal { padding-left: 27px; }
  .meal-list {
    list-style: none; padding-left: 78px;
    font-family: "Open Sans", Arial, sans-serif; font-size: 14.5px; line-height: 22px;
  }
  .meal-list li::before { content: "•"; position: absolute; margin-left: -22px; }
  .note { top: 603px; line-height: 21.2px; }
  .gratuity { top: 691px; display: flex; align-items: baseline; gap: 12px; }
  .capacity-head { top: 727px; }
  .capacity { top: 758px; line-height: 22px; }
  .services-head { top: 869px; }
  .services { top: 919px; line-height: 21.8px; }
  .services b { font-weight: 700; }
</style>
</head>
<body>
<main class="sheet">
  <svg class="backdrop" width="849" height="1200" viewBox="0 0 849 1200" aria-hidden="true">
    <polygon points="0,0 849,0 849,368 40,18 0,18" fill="var(--paper)"/>
    <path d="M28 14 H820 V28 H836 V1168 H822 V1184 H28 V1170 H12 V28 H28 Z"
          fill="none" stroke="var(--gold)" stroke-width="2.5"/>
    <path d="M40 26 H808 V40 H824 V1158 H810 V1172 H40 V1158 H24 V40 H40 Z"
          fill="none" stroke="var(--gold)" stroke-width="1.5"/>
  </svg>

  <div class="brand">COPPER KETTLE</div>

  <h1 class="page-title">PRIVATE DINING ROOM</h1>

  <p class="block intro">Thank you for your interest in reserving Copper Kettle’s Private Dining Room! We are more than happy to go above and beyond to make the most of your group experience – below are some helpful details about the room that will help you plan your event. See pages 2-4 for menu options.</p>

  <h2 class="block section-head minimum-head">Food and Beverage Room Minimum (before tax&amp;gratuity):</h2>

  <div class="block meals">
    <p class="meal">LUNCH (Eating Prior to 3pm)</p>
    <ul class="meal-list"><li>Every day: $200 minimum</li></ul>
    <p class="meal">DINNER (Eating After 3pm)</p>
    <ul class="meal-list">
      <li>Sun-Thurs: $400 minimum</li>
      <li>Fri-Sat: $600 minimum</li>
    </ul>
  </div>

  <p class="block note">*If you do not reach the room minimum, we simply charge you the remaining balance to get your bill up to the room minimum. For example, if you book a Thursday lunch meeting and spend $165 in food and beverage (before tax and gratuity) we will charge $35 to the bill to get to the minimum of $200.</p>

  <div class="block gratuity">
    <h2 class="section-head">Gratuity:</h2>
    <span>There will be an automatic 18% gratuity added on to the bill</span>
  </div>

  <h2 class="block section-head capacity-head">Room Capacity/Layout Options:</h2>
  <div class="block capacity">
    <p>Sit down dinner setting – accommodates up to 50 people</p>
    <p>Happy Hour setting – up to 60 people (at one time, can hold more if guests are coming and going)</p>
    <p>Layout options – U-Shaped (up to 24 ppl) , Large Square (up to 20 ppl), &nbsp;Other (up to 50 ppl)</p>
    <p>Open to Patio – have the option to open three double doors from room to patio and block off a section of the patio right outside of the room, only available if weather is permitting</p>
  </div>

  <h2 class="block section-head services-head">Miscellaneous Services:</h2>
  <div class="block services">
    <p><b>Linen Fee</b> (ivory tablecloths on all tables)<b>:</b> $25 total</p>
    <p><b>Cake Cutting Fee</b> (for any licensed bakery dessert, cannot bring anything homemade): $10</p>
    <p><b>Corkage Fee</b> (per bottle of wine brought in): $12</p>
    <p><b>Audio Visual:</b> 60” LED Smart TV for presentations, picture slideshows, or watching the big game. Project wirelessly with CastBeam Stream or with hookups via VGA, mini display port, or HDMI cables.</p>
    <p><b>Decorations:</b> We are happy to assist in setting up any decorations – let us know what you are thinking prior to the event and we can approve.</p>
  </div>
</main>
</body>
</html>
```